Reach Crafters Unique Marketing Website Design

I am starting a new company that is a thought leader in the marketing consulting space. The company is called Reach Crafters. We intend to build a Wordpress site on the Astra Theme with the Spectra builder. Our goal is to become the leading voice that empowers high-ticket service business leaders to become Reach Crafters by equipping them with the cutting-edge frameworks and decision grade intelligence taught in leading business schools. What we are looking for is a website design that is clean and professional, making some use of white space well also being eye catching and distinctive in the consulting space. We will probably want to have a video on the homepage not in the hero section, but just below to explain the company and what we do. Our tagline is "Be found. Be chosen." I have attached a brand guide with some messaging, our typography choices, and our color system. The full site will have a primary nav that is four pages - About us, Services, Insights (essentially a blog), and Contact Us. The goal of this project is to develop an art direction that I can give to a designer to build loads of new pages.

Target Market(s)

Business owners (mostly male) from 30-60 years old, looking to fix their sales and marketing funnel.

Industry/Entity Type

Marketing consulting

Font styles to use
Sans Serif

Requirements
Must have
• A clean, professional design that builds trust with owners of high-ticket service businesses. We need a space for explainer video, and sections that tell prospects what we do. Would also like to have a blog carousel.
Nice to have
• Social feeds, if possible. See attached documents for colors and fonts.
Should not have
• Our feel is professional enough to be trustworthy, but unique enough to be memorable. Cartoon ideas do not meet the professional test, and we do not want the website to appear feminine.

```html
<!DOCTYPE html>
<html lang="en">
<head>
<meta charset="utf-8">
<title>Reach Crafters — Be Found. Be Chosen.</title>
<link rel="stylesheet" href="https://fonts.googleapis.com/css2?family=Oswald:wght@500;600;700&family=Inter:wght@400;500;600;700&family=Libre+Baskerville:wght@400;700&family=Poppins:wght@400;500;600&display=swap">
<style>
:root{
  --blue:#2440f0;
  --navy:#070d26;
  --ink:#1e1e24;
  --band:#0f172f;
  --band2:#1d1f26;
  --text:#333;
  --muted:#555;
  --white:#fff;
  --green:#1f9d55;
}
*{box-sizing:border-box;margin:0;padding:0}
html,body{width:1200px;height:4559px;overflow:hidden;background:var(--white)}
body{position:relative;font-family:"Inter",sans-serif;color:var(--text)}
.abs{position:absolute}
.center{left:0;width:1200px;text-align:center}
.h2{font-family:"Oswald",sans-serif;font-weight:600;font-size:32px;letter-spacing:.5px;color:var(--ink)}
.h2 .accent{color:var(--blue)}
.kicker{font-family:"Inter",sans-serif;font-weight:600;font-size:14px;letter-spacing:.5px;color:var(--ink)}
.lead{font-size:15.5px;line-height:29px;color:#333}
.on-dark{color:var(--white)}
.btn{display:inline-block;background:var(--blue);color:#fff;font-weight:700;font-size:14.5px;border-radius:30px;text-align:center}
/* header */
.site-header{top:0;left:0;width:1200px;height:85px;background:#fff}
.brand{left:110px;top:26px;font-family:"Inter",sans-serif;font-weight:700;font-size:29px;color:var(--ink);letter-spacing:-.3px;white-space:nowrap}
.nav-link{top:33px;font-size:14.5px;font-weight:500;color:#222;white-space:nowrap}
.nav-link.active{color:var(--blue);font-weight:600}
.nav-cta{left:949px;top:18px;width:140px;height:47px;line-height:47px;font-size:15px}
/* hero */
.hero-title{top:230px;font-family:"Oswald",sans-serif;font-weight:600;font-size:74px;color:#fff;letter-spacing:1px}
.hero-sub{top:325px;font-size:16px;line-height:30px;color:#e8ebf5}
/* values */
.value-icon{width:92px;height:92px;border-radius:50%;background:#fff;display:flex;align-items:center;justify-content:center}
.value-label{font-family:"Libre Baskerville",serif;font-weight:700;font-size:14.5px;color:#fff;text-align:center;line-height:29px;width:300px}
/* service cards */
.svc-img{width:222px;height:266px;border-radius:22px}
.svc-label{font-family:"Libre Baskerville",serif;font-weight:700;font-size:16px;color:#222;text-align:center;width:222px}
.svc-pop{background:#fff;border-radius:18px;box-shadow:0 6px 14px rgba(0,0,0,.18);text-align:center;padding:14px 10px}
.svc-pop h4{font-family:"Libre Baskerville",serif;font-size:16px;line-height:21px;color:#222;font-weight:700}
.svc-pop p{font-size:12.5px;line-height:17px;color:#444;margin-top:6px}
/* testimonials */
.t-card{width:397px;height:205px;background:#fff;border-radius:30px}
.t-avatar{width:116px;height:116px;border-radius:50%;background:linear-gradient(160deg,#b9bcc2,#5a5f68);border:3px solid #fff}
.t-body{font-family:"Poppins",sans-serif;font-size:14px;line-height:24px;color:#333}
.stars{color:#f4b400;font-size:16px;letter-spacing:1px}
.t-name{font-family:"Poppins",sans-serif;font-weight:600;font-size:15px;color:#111;white-space:nowrap}
.t-co{font-family:"Poppins",sans-serif;font-size:12px;color:#555;margin-left:14px;font-weight:400}
/* blog */
.blog-card{border:1px solid #ddd;background:#fff}
.blog-title{font-family:"Libre Baskerville",serif;font-weight:700;font-size:15px;line-height:23px;color:#222}
.blog-ex{font-size:13px;line-height:21px;color:#666}
.date{font-family:"Poppins",sans-serif;font-weight:500;font-size:15px;color:var(--blue)}
/* footer */
.f-head{font-family:"Poppins",sans-serif;font-weight:600;font-size:21px;color:#fff;white-space:nowrap}
.f-list{list-style:none;font-family:"Poppins",sans-serif;font-size:14px;color:#fff}
.f-list li{height:31px;display:flex;align-items:center;gap:12px}
.f-contact{font-family:"Poppins",sans-serif;font-size:14px;color:#fff;display:flex;align-items:center;gap:14px;height:38px;white-space:nowrap}
.f-dot{width:36px;height:36px;border-radius:50%;background:var(--blue);display:flex;align-items:center;justify-content:center}
</style>
</head>
<body>

<!-- Header -->
<header class="abs site-header">
  <div class="abs brand">REACH CRAFTERS</div>
  <nav>
    <span class="abs nav-link active" style="left:561px">HOME</span>
    <span class="abs nav-link" style="left:638px">ABOUT US</span>
    <span class="abs nav-link" style="left:745px">SERVICES</span>
    <span class="abs nav-link" style="left:847px">INSIGHTS</span>
  </nav>
  <a class="abs btn nav-cta">CONTACT US</a>
</header>

<!-- Hero -->
<section class="hero">
  <svg class="abs" style="top:85px;left:0" width="1200" height="605" viewBox="0 0 1200 605">
    <defs>
      <radialGradient id="heroGlow" cx="0.3" cy="0.45" r="0.7">
        <stop offset="0" stop-color="#13325a"/><stop offset="0.6" stop-color="#0a1430"/><stop offset="1" stop-color="#050a1e"/>
      </radialGradient>
    </defs>
    <path d="M0 0H1200V490Q600 700 0 500Z" fill="url(#heroGlow)" role="img" aria-label="Dark abstract particle wave background"/>
    <path d="M0 490Q300 560 560 600Q300 590 0 540Z" fill="#3c3c42"/>
    <path d="M1200 500Q1000 590 640 605Q1000 600 1200 545Z" fill="var(--blue)"/>
  </svg>
  <h1 class="abs center hero-title">BE FOUND.BE CHOSEN.</h1>
  <p class="abs center hero-sub">We help high-ticket service businesses engineer demand using decision-grade intelligence and proven<br>frameworks taught in the world's leading business schools.</p>
  <a class="abs btn" style="left:474px;top:405px;width:252px;height:46px;line-height:46px">EXPLORE OUR APPROACH</a>
  <svg class="abs" style="left:586px;top:548px" width="28" height="56" viewBox="0 0 28 56">
    <rect x="2" y="2" width="24" height="36" rx="12" fill="none" stroke="#fff" stroke-width="2"/>
    <line x1="14" y1="9" x2="14" y2="16" stroke="#fff" stroke-width="2"/>
    <path d="M14 42V53M9 48L14 53L19 48" fill="none" stroke="#fff" stroke-width="1.6"/>
  </svg>
</section>

<!-- Who we are -->
<section>
  <h2 class="abs center h2" style="top:788px">WHAT REACH CRAFTERS DOES || <span class="accent">AND WHY IT WORKS</span></h2>
  <div class="abs center kicker" style="top:844px">WHO WE ARE</div>
  <p class="abs center lead" style="top:879px">Most service businesses rely on referrals, reputation, or reactive marketing to grow. Reach Crafters helps leaders replace<br>guesswork with clarity by designing demand systems rooted in strategy, data, and executive-level decision making.</p>
  <div class="abs" style="left:145px;top:945px;width:911px;height:446px;background:linear-gradient(135deg,#3a2c22,#6e5440 50%,#b8a890)" role="img" aria-label="Explainer video still: team collaborating around a table"></div>
  <svg class="abs" style="left:578px;top:1146px" width="44" height="44" viewBox="0 0 44 44"><circle cx="22" cy="22" r="22" fill="var(--blue)"/><path d="M17 13L31 22L17 31Z" fill="#fff"/></svg>
</section>

<!-- Values band -->
<section>
  <svg class="abs" style="top:1488px;left:0" width="1200" height="570" viewBox="0 0 1200 570">
    <path d="M0 70Q600 -70 1200 70V480Q600 640 0 480Z" fill="var(--band)" role="img" aria-label="Dark blue textured background"/>
  </svg>
  <h2 class="abs center h2 on-dark" style="top:1574px">REFERRALS ARE NOT || A GROWTH STRATEGY</h2>
  <div class="abs center kicker on-dark" style="top:1631px">OUR VALUES</div>
  <p class="abs center lead on-dark" style="top:1662px;font-size:15px;line-height:27px">High-ticket service firms don't struggle because they lack expertise. They struggle because the market doesn't clearly<br>understand why to choose them.</p>
  <p class="abs center on-dark" style="top:1744px;font-size:15px">Without a clear demand strategy, even exceptional firms become:</p>
  <svg class="abs" style="left:330px;top:1830px" width="540" height="60" viewBox="0 0 540 60">
    <path d="M0 20Q70 10 130 40Q200 65 230 20" fill="none" stroke="#cfd4e4" stroke-dasharray="2 3"/>
    <path d="M310 20Q370 10 430 40Q490 65 540 20" fill="none" stroke="#cfd4e4" stroke-dasharray="2 3"/>
  </svg>
  <div class="abs value-icon" style="left:242px;top:1809px">
    <svg width="50" height="50" viewBox="0 0 50 50" fill="none" stroke="var(--blue)" stroke-width="2"><circle cx="20" cy="20" r="10"/><path d="M15 30v6h10v-6M17 40h6"/><circle cx="34" cy="30" r="7"/><path d="M39 35l6 6"/></svg>
  </div>
  <div class="abs value-icon" style="left:560px;top:1809px">
    <svg width="50" height="50" viewBox="0 0 50 50" fill="none" stroke="var(--blue)" stroke-width="2"><circle cx="25" cy="14" r="7"/><circle cx="12" cy="26" r="6"/><circle cx="38" cy="26" r="6"/><path d="M22 21v5h6v-5M10 32v4h4v-4M36 32v4h4v-4M25 28v14M12 38l13 6 13-6"/></svg>
  </div>
  <div class="abs value-icon" style="left:878px;top:1809px">
    <svg width="50" height="50" viewBox="0 0 50 50" fill="none" stroke="var(--blue)" stroke-width="2"><circle cx="30" cy="20" r="9"/><path d="M26 29v5h8v-5"/><path d="M8 30l12-6v14l-12-6zM20 26h4v10h-4"/></svg>
  </div>
  <div class="abs value-label" style="left:138px;top:1913px">HARD TO DISCOVER</div>
  <div class="abs value-label" style="left:456px;top:1913px">DIFFICULT TO DIFFERENTIATE</div>
  <div class="abs value-label" style="left:774px;top:1913px">FORCED TO COMPETE ON<br>REPUTATION ALONE</div>
</section>

<!-- Services -->
<section>
  <h2 class="abs center h2" style="top:2152px">WE BUILD DEMAND || <span class="accent">NOT JUST MARKETING</span></h2>
  <div class="abs center kicker" style="top:2207px">WHAT WE DO</div>
  <p class="abs center lead" style="top:2241px">Reach Crafters works with founders and leadership teams to create market clarity, positioning authority, and<br>predictable demand.</p>
  <div class="abs svc-img" style="left:110px;top:2328px;background:linear-gradient(160deg,#1a2236,#33456a 60%,#0c1222)" role="img" aria-label="Businessman holding a glowing strategy diagram"></div>
  <div class="abs svc-img" style="left:362px;top:2328px;background:linear-gradient(160deg,#0c1e5a,#2a5fd0 50%,#7a3fbf)" role="img" aria-label="Digital head of light representing intelligence"></div>
  <div class="abs svc-img" style="left:614px;top:2328px;background:linear-gradient(160deg,#062a3a,#0f7fa6 55%,#0a1a24)" role="img" aria-label="Glowing circuit chip with a cart symbol"></div>
  <div class="abs svc-img" style="left:866px;top:2328px;background:linear-gradient(160deg,#2b3440,#6a7480 55%,#3a4654)" role="img" aria-label="Advisors reviewing data screens in an office"></div>
  <div class="abs svc-pop" style="left:375px;top:2525px;width:198px;height:135px">
    <h4>Decision-Grade Intelligence</h4>
    <p>Replace assumptions with insight using rigorous analysis that supports confident.</p>
  </div>
  <div class="abs svc-label" style="left:110px;top:2612px">Demand Strategy</div>
  <div class="abs svc-label" style="left:614px;top:2612px">Revenue Architecture</div>
  <div class="abs svc-label" style="left:866px;top:2612px">Executive Advisory</div>
</section>

<!-- Testimonials -->
<section>
  <svg class="abs" style="top:2752px;left:0" width="1200" height="548" viewBox="0 0 1200 548">
    <path d="M0 60Q600 -60 1200 60V450Q600 620 0 450Z" fill="var(--band2)"/>
  </svg>
  <h2 class="abs center h2 on-dark" style="top:2838px">CLIENT || TESTIMONIALS</h2>
  <div class="abs center kicker on-dark" style="top:2896px">OUR REVIEWS</div>
  <svg class="abs" style="left:58px;top:3045px" width="26" height="26" viewBox="0 0 26 26"><circle cx="13" cy="13" r="11.5" fill="none" stroke="#ccc" stroke-width="1.4"/><path d="M15 8l-5 5 5 5" fill="none" stroke="#ccc" stroke-width="1.6"/></svg>
  <svg class="abs" style="left:1117px;top:3045px" width="26" height="26" viewBox="0 0 26 26"><circle cx="13" cy="13" r="11.5" fill="none" stroke="#ccc" stroke-width="1.4"/><path d="M11 8l5 5-5 5" fill="none" stroke="#ccc" stroke-width="1.6"/></svg>

  <div class="abs t-card" style="left:193px;top:2953px"></div>
  <div class="abs t-avatar" style="left:140px;top:2997px" role="img" aria-label="Client portrait"></div>
  <div class="abs stars" style="left:276px;top:2983px">★★★★★</div>
  <p class="abs t-body" style="left:276px;top:3013px;width:290px">We work with firms where expertise is already proven — and growth depends on strategic clarity, not more tactics.</p>
  <div class="abs t-name" style="left:283px;top:3100px">Mark Ellis<span class="t-co">Company Name</span></div>

  <div class="abs t-card" style="left:690px;top:2953px"></div>
  <div class="abs t-avatar" style="left:638px;top:2997px" role="img" aria-label="Client portrait"></div>
  <div class="abs stars" style="left:773px;top:2983px">★★★★★</div>
  <p class="abs t-body" style="left:773px;top:3013px;width:290px">We work with firms where expertise is already proven — and growth depends on strategic clarity, not more tactics.</p>
  <div class="abs t-name" style="left:780px;top:3100px">Mark Ellis<span class="t-co">Company Name</span></div>
</section>

<!-- Blog -->
<section>
  <h2 class="abs center h2" style="top:3392px">LATEST || <span class="accent">BLOG</span></h2>
  <div class="abs center kicker" style="top:3446px;word-spacing:4px">OUR INSIGHTS</div>

  <div class="abs blog-card" style="left:110px;top:3505px;width:477px;height:424px"></div>
  <div class="abs" style="left:111px;top:3506px;width:475px;height:256px;background:linear-gradient(135deg,#c9ced6,#8b96a6 55%,#e6e8ec)" role="img" aria-label="Colleagues reviewing a tablet together"></div>
  <div class="abs" style="left:111px;top:3731px;height:31px;padding:0 14px;background:var(--green);color:#fff;font-family:Poppins,sans-serif;font-weight:600;font-size:14px;line-height:31px">▦ 27, JAN 2026</div>
  <div class="abs blog-title" style="left:135px;top:3783px;width:360px">Lorem ipsum dolor sit amet, consectetur adipiscing elit,</div>
  <div class="abs blog-ex" style="left:135px;top:3834px;white-space:nowrap">Excepteur sint occaecat cupidatat non proident, sunt in culpa</div>
  <a class="abs btn" style="left:135px;top:3866px;width:124px;height:39px;line-height:39px;font-size:13.5px">LEARN MORE</a>

  <div class="abs blog-card" style="left:611px;top:3503px;width:478px;height:201px"></div>
  <div class="abs" style="left:625px;top:3518px;width:148px;height:170px;background:linear-gradient(135deg,#1a1e24,#4a5360 60%,#2c3038)" role="img" aria-label="Laptop with glowing data icons"></div>
  <div class="abs date" style="left:838px;top:3530px">▦ 28 JAN 2026</div>
  <div class="abs blog-title" style="left:840px;top:3560px;width:228px;font-size:14.5px">Lorem ipsum dolor sit amet, consectetur adipiscing elit,</div>
  <div class="abs blog-ex" style="left:840px;top:3609px;width:238px;font-size:12.5px">Excepteur sint occaecat cupidatat non proident, sunt in culpa qui officia deserunt mollit anim id est laborum.</div>

  <div class="abs blog-card" style="left:611px;top:3722px;width:478px;height:201px"></div>
  <div class="abs" style="left:625px;top:3737px;width:148px;height:170px;background:linear-gradient(135deg,#1f2a44,#4b5f86 60%,#c8ccd4)" role="img" aria-label="Presenter explaining charts on a screen"></div>
  <div class="abs date" style="left:838px;top:3749px">▦ 28 JAN 2026</div>
  <div class="abs blog-title" style="left:840px;top:3779px;width:228px;font-size:14.5px">Lorem ipsum dolor sit amet, consectetur adipiscing elit,</div>
  <div class="abs blog-ex" style="left:840px;top:3828px;width:238px;font-size:12.5px">Excepteur sint occaecat cupidatat non proident, sunt in culpa qui officia deserunt mollit anim id est laborum.</div>
</section>

<!-- Footer -->
<footer>
  <svg class="abs" style="top:4040px;left:0" width="1200" height="519" viewBox="0 0 1200 519">
    <path d="M0 100Q500 0 1200 20V519H0Z" fill="#000"/>
    <path d="M0 100Q300 20 620 8Q300 50 0 150Z" fill="var(--blue)"/>
  </svg>
  <div class="abs f-head" style="left:89px;top:4183px">Quick Links</div>
  <ul class="abs f-list" style="left:89px;top:4225px">
    <li>➜ Home</li><li>➜ About Us</li><li>➜ Services</li><li>➜ Insights</li><li>➜ Contact Us</li>
  </ul>
  <div class="abs f-head" style="left:289px;top:4183px">Other Links</div>
  <ul class="abs f-list" style="left:289px;top:4225px">
    <li>➜ FAQ</li><li>➜ Terms of Use</li><li>➜ Privacy Policy</li><li>➜ Support Links</li><li>➜ Conditions</li>
  </ul>
  <div class="abs f-head" style="left:500px;top:4183px">Contact Us</div>
  <div class="abs f-contact" style="left:500px;top:4233px"><span class="f-dot"><svg width="14" height="16" viewBox="0 0 14 16"><path d="M7 1a5 5 0 0 1 5 5c0 4-5 9-5 9S2 10 2 6a5 5 0 0 1 5-5z" fill="#fff"/><circle cx="7" cy="6" r="2" fill="var(--blue)"/></svg></span>Company Name,United State.</div>
  <div class="abs f-contact" style="left:500px;top:4293px"><span class="f-dot"><svg width="16" height="12" viewBox="0 0 16 12"><rect x="0.5" y="0.5" width="15" height="11" fill="#fff"/><path d="M1 1l7 6 7-6" fill="none" stroke="var(--blue)"/></svg></span>info@reachcrafters.co</div>
  <div class="abs f-contact" style="left:500px;top:4353px"><span class="f-dot"><svg width="14" height="14" viewBox="0 0 14 14"><path d="M3 1l3 3-2 2c1 2 2 3 4 4l2-2 3 3-2 2C6 13 1 8 1 3z" fill="#fff"/></svg></span>+1 555 0142 7788</div>
  <div class="abs f-head" style="left:820px;top:4183px">Sign Up to Our Newsletter</div>
  <p class="abs" style="left:820px;top:4228px;width:285px;font-family:Poppins,sans-serif;font-size:13.5px;line-height:30px;color:#fff">Lorem ipsum dolor sit amet,consectetur adipiscing elit,adipiscing elit.</p>
  <div class="abs" style="left:822px;top:4303px;font-family:Poppins,sans-serif;font-size:14px;color:#fff">Email</div>
  <div class="abs" style="left:820px;top:4328px;width:275px;height:1px;background:#fff"></div>
  <a class="abs btn" style="left:828px;top:4366px;width:146px;height:50px;line-height:50px;font-family:Poppins,sans-serif;font-weight:600;font-size:16px">Subscribe</a>
  <div class="abs" style="left:89px;top:4484px;width:1006px;height:1px;background:#555"></div>
  <div class="abs center" style="top:4510px;font-family:Poppins,sans-serif;font-weight:500;font-size:13.5px;color:#fff">COPYRIGHTS@2026.COMPANY NAME.ALL RIGHTS RESERVED</div>
</footer>

</body>
</html>
```